Redesign Canvas Art E-Commerce Website

Help! I hired a couple of companies on Brisklo.com to build and design an e-commerce website for me. After three long and painful months, I have one that I believe is functional on the back-end, but aesthetically on the front end is a mess.

We are a small family business that will take your digital photo and manipulate it into a digitally created oil, watercolor or impressionist style pieces of artwork that we print on museum quality, gallery grade canvas and ship to the customer, ready to hang.

We are looking to create an e-commerce website where a customer can choose their art style, upload a photo, choose their canvas size and orientation (horizontal or vertical) and checkout. Within 48 hours, we will send them back a proof of their newly created, customized artwork for them to approve or not approve. If they approve, we print, package and ship them the product. If they do not approve, we offer unlimited revisions until they are happy.

As I mentioned, the back end functionality is already there, just need design help. No coding required

Here is a link to the development page that they created: https://plumwickstudio.com/development/

As you can see, it looks off...doesnt line up properly, wasted space, weird font. Feel free to either correct the homepage they created or design an entirely new page. I am attaching some examples of before and after photos of artwork for reference. I also think the testimonials page and shop page can use a little style. The content is there and accurate, it just doesn't look pretty. Please keep in mind that our customers will probably not be very tech savvy. The customers will probably be sending us pics of kids, grandkids, pets, family portraits, vacation photos, etc.

Here is one of our competitors - www.gildavantry.com
Their website looks clean and inviting.

Thank you in advance! Im looking forward to seeing the results. I am including our logo in the attachments (I do not have it in a vector file, just a jpeg)

Target Market(s)

Non tech-savvy indiduals, 30-70 years old

Industry/Entity Type

Please look at https://plumwickstudio.com/development/ to see various pages and what the other designers did

Number of Pages Required

1 page

Requirements
Must have
• Verbiage on pages leave "as is" but feel free to change styles. Would like to keep existing four categories on homepage
Nice to have
• Warm and inviting homepage that evokes emotion

```html
<!DOCTYPE html>
<html lang="en">
<head>
<meta charset="utf-8">
<title>Easel House — Digital Photos Into Wall Art</title>
<link href="https://fonts.googleapis.com/css2?family=Lato:wght@400;700;900&family=Playball&display=swap" rel="stylesheet">
<style>
:root{
  --red:#e03a13;
  --red-dark:#c92e0c;
  --ink:#1d1d1d;
  --muted:#555;
  --blush:#f9e6e2;
  --cream:#fdf3d0;
  --gold:#f5c518;
  --grey:#f4f4f4;
  --black:#000;
}
*{box-sizing:border-box;margin:0;padding:0}
html,body{width:1200px;height:4511px;overflow:hidden}
body{position:relative;font-family:'Lato',sans-serif;color:var(--ink);background:#fff}
.abs{position:absolute}
.script{font-family:'Playball',cursive;font-weight:400}
.btn{position:absolute;display:flex;align-items:center;justify-content:center;background:var(--red);color:#fff;font-weight:700;border-radius:3px;box-shadow:0 3px 6px rgba(0,0,0,.18)}
.ph{position:absolute}

/* top bar */
.topbar{left:0;top:0;width:1200px;height:60px;background:var(--red);color:#fff;font-size:14px;font-weight:700;letter-spacing:1.5px;display:flex;align-items:center;justify-content:center}
.header{left:0;top:60px;width:1200px;height:83px;border-bottom:2px solid #e5e5e5}
.brand{left:102px;top:22px;display:flex;align-items:center;gap:10px;font-size:30px;font-weight:700;color:var(--ink)}
.brand .dot{width:22px;height:22px;border-radius:50%;background:var(--red)}
.nav{left:365px;top:32px;display:flex;gap:40px;font-size:15px}
.cart{left:922px;top:32px}
.contact-btn{left:983px;top:20px;width:117px;height:41px;font-size:15px}

.catstrip{left:90px;top:170px;width:1020px;height:42px;display:flex;align-items:center;gap:12px;font-size:13px;color:#555}
.chip{display:flex;align-items:center;gap:8px;height:42px;padding:0 10px 0 0;border:1px solid #eee;background:#fff}
.chip i{display:block;width:40px;height:40px}
.arrow-sm{width:18px;height:18px;border-radius:50%;border:1px solid #ddd;display:flex;align-items:center;justify-content:center;color:var(--red);font-size:12px}

/* hero */
.hero-bg{left:110px;top:254px;width:978px;height:534px;background:var(--blush)}
.welcome{left:166px;top:328px;font-size:15px;font-weight:700;letter-spacing:2.5px;color:var(--red)}
.hero-title{left:168px;top:380px;width:480px;font-size:40px;line-height:68px;color:var(--ink)}
.hero-copy{left:166px;top:528px;width:460px;font-size:15px;line-height:30px;color:#333}
.rating{left:166px;top:692px;font-size:18px;display:flex;align-items:center;gap:14px}
.rating .stars{color:var(--gold);font-size:14px;letter-spacing:1px}
.rating .reviews{font-size:15px;color:#444}
.hero-frame{left:681px;top:322px;width:333px;height:405px;border:3px solid var(--red);border-radius:10px;background:#fff}
.hero-frame .ph{inset:8px;background:linear-gradient(160deg,#cfd7c9,#7f8f6a 55%,#89b8cf)}
.circ{position:absolute;width:30px;height:30px;border-radius:50%;background:#fff;box-shadow:0 2px 5px rgba(0,0,0,.2);display:flex;align-items:center;justify-content:center;color:var(--red);font-weight:900;font-size:16px}

/* categories */
.sec-title{position:absolute;left:0;width:1200px;text-align:center;font-size:42px}
.sec-sub{left:250px;top:926px;width:700px;text-align:center;font-size:14px;line-height:29px;color:#444}
.card{position:absolute;text-align:center}
.card h3{font-weight:400;font-size:19px}
.card .stars{color:var(--red);font-size:16px;letter-spacing:1px}
.card p{font-size:12px;line-height:26px;color:#555}
.card-side{width:279px;height:409px;top:1085px;background:var(--cream)}
.card-side .ph{left:30px;top:0;width:219px;height:232px;border-radius:4px}
.card-side h3{position:absolute;top:236px;width:100%}
.card-side .stars{position:absolute;top:270px;width:100%}
.card-side p{position:absolute;top:296px;left:20px;width:239px}
.card-side .small-btn{position:absolute;left:76px;top:388px;width:127px;height:36px;background:var(--gold);color:#222;font-size:12px;font-weight:700;display:flex;align-items:center;justify-content:center;border-radius:2px}
.card-main{left:422px;top:1048px;width:358px;height:482px;background:var(--blush)}
.card-main .ph{left:48px;top:-35px;width:262px;height:287px;border-radius:2px}
.card-main h3{position:absolute;top:272px;width:100%;font-size:23px}
.card-main .stars{position:absolute;top:314px;width:100%;font-size:18px}
.card-main p{position:absolute;top:344px;left:28px;width:302px;font-size:14px;line-height:29px}
.big-arrow{position:absolute;width:30px;height:30px;border-radius:50%;background:var(--red);color:#fff;display:flex;align-items:center;justify-content:center;font-weight:900}

/* about */
.about-bg{left:0;top:1650px;width:1200px;height:568px;background:var(--grey)}
.about-photo{left:405px;top:1650px;width:795px;height:568px;background:radial-gradient(ellipse at 55% 45%,#f3cbbd,#f5e4de 55%,#fbf4f1)}
.about-card{left:110px;top:1734px;width:463px;height:377px;background:#fff;box-shadow:0 4px 16px rgba(0,0,0,.1);border-radius:4px;text-align:center}
.about-card h2{margin-top:24px;font-size:38px}
.about-card p{margin:16px 14px 0;font-size:14px;line-height:29px;color:#333}

/* why */
.why{position:absolute;width:300px;text-align:center}
.why h4{font-size:17px;font-weight:700;margin-top:12px}
.why p{font-size:12.5px;line-height:26px;color:#555;margin-top:4px}

/* gallery */
.gallery-bg{left:0;top:2665px;width:1200px;height:797px;background:#f7f7f7}

/* deal */
.deal{left:0;top:3462px;width:1200px;height:538px;background:linear-gradient(115deg,#e8451a,#cf3310 55%,#e04216)}
.badge{left:88px;top:3623px;width:210px;height:210px;border-radius:50%;border:4px solid #fff;background:var(--red-dark);color:#fff;text-align:center;padding-top:40px}
.badge .b1{font-size:36px;font-weight:900;letter-spacing:2px}
.badge .b2{font-size:14px;font-weight:700}
.badge .b3{font-size:36px;font-weight:900;letter-spacing:2px}
.badge .b4{font-size:10px;color:var(--gold)}
.deal-text{left:349px;top:3520px;width:420px;color:#fff}
.deal-text .pct{font-size:40px;font-weight:700;letter-spacing:1px}
.deal-text .sub{font-size:26px;font-weight:700;letter-spacing:1px;margin-top:6px}
.deal-text p{font-size:14px;line-height:26px;margin-top:18px}
.timer{position:absolute;top:3788px;width:60px;height:60px;border:1.5px solid #fff;color:#fff;text-align:center;padding-top:6px}
.timer b{display:block;font-size:22px}
.timer span{font-size:13px}
.learn{left:350px;top:3882px;width:167px;height:51px;background:#fff;color:#222;font-size:16px;font-weight:700;border-radius:3px;box-shadow:0 3px 8px rgba(0,0,0,.2);display:flex;align-items:center;justify-content:center}
.deal-photo{left:785px;top:3557px;width:304px;height:304px;border-radius:50%;border:4px solid #fff;background:linear-gradient(150deg,#c9e0ef,#e9c9a8 55%,#c87a44)}

/* footer */
.site-footer{color:#fff}
.footer{left:0;top:4000px;width:1200px;height:511px;background:var(--black)}
.flinks{left:154px;top:4091px;width:892px;display:flex;justify-content:space-between;font-size:15px;color:#fff}
.flinks span.sep{font-size:8px;line-height:20px}
.fline{background:#666}
.fbrand{left:490px;top:4150px;width:220px;height:60px;background:#000;display:flex;align-items:center;justify-content:center;gap:10px;font-size:30px;font-weight:700;color:#fff}
.fbrand .dot{width:20px;height:20px;border-radius:50%;background:var(--red)}
.fcol{position:absolute;top:4242px;text-align:center;color:#fff}
.fcol h5{font-size:20px;font-weight:400;letter-spacing:.5px}
.fcol p{font-size:13.5px;line-height:28px;margin-top:14px}
.soc{display:flex;gap:22px;justify-content:center;margin-top:16px}
.soc i{width:22px;height:22px;border-radius:50%;background:var(--red);display:block}
.copy{left:110px;top:4455px;font-size:13px;color:#fff}
.pay{top:4454px;width:36px;height:18px;background:#fff;border-radius:2px}
</style>
</head>
<body>

<div class="abs topbar">FREE SHIPPING FOR ALL USA &amp; ORDERS</div>

<header class="abs header">
  <div class="abs brand"><span class="dot"></span>Easel House</div>
  <nav class="abs nav"><span>Home</span><span>Shop</span><span>Testimonials</span><span>About Us</span><span>FAQs</span><span>My Orders</span></nav>
  <svg class="abs cart" width="22" height="20" viewBox="0 0 22 20"><path d="M1 2h4l3 11h10l2-8H7" fill="none" stroke="#111" stroke-width="2"/><circle cx="9" cy="17" r="1.6" fill="#111"/><circle cx="17" cy="17" r="1.6" fill="#111"/><circle cx="19" cy="3" r="3" fill="#e03a13"/></svg>
  <div class="btn contact-btn">Contact Us</div>
</header>

<div class="abs catstrip">
  <span class="arrow-sm">‹</span>
  <div class="chip"><i role="img" aria-label="Best seller artwork thumbnail" style="background:#b67d4f"></i>Best Sellers</div>
  <div class="chip"><i role="img" aria-label="New portrait thumbnail" style="background:#6f8a4a"></i>New portraits</div>
  <div class="chip"><i role="img" aria-label="Puppy portrait thumbnail" style="background:#a6a39a"></i>Puppy portraits</div>
  <div class="chip"><i role="img" aria-label="Couple portrait thumbnail" style="background:#8fa08e"></i>Couple portraits</div>
  <div class="chip"><i role="img" aria-label="Fishing portrait thumbnail" style="background:#7d8ea3"></i>Fishing portraits</div>
  <div class="chip"><i role="img" aria-label="Horse portrait thumbnail" style="background:#7a4a2a"></i>Horse portraits</div>
  <span class="arrow-sm">›</span>
</div>

<section>
  <div class="abs hero-bg"></div>
  <div class="abs welcome">WELCOME TO EASEL HOUSE</div>
  <h1 class="abs hero-title script">Turn Your Digital Photos Into<br>One of a Kind Wall Art</h1>
  <p class="abs hero-copy">At Easel House, we take your digital photo and turn it into a one-of-a-kind piece of artwork!</p>
  <div class="btn" style="left:166px;top:613px;width:167px;height:51px;font-size:16px">Get Started</div>
  <div class="abs rating"><span>Excellant</span><span class="stars">★★★★★</span><span class="reviews">(10302+ REVIEWS)</span></div>
  <div class="abs hero-frame"><div class="ph" role="img" aria-label="Painted portrait of a grandmother hugging a grandfather"></div></div>
  <div class="circ" style="left:666px;top:510px">‹</div>
  <div class="circ" style="left:998px;top:510px">›</div>
</section>

<section>
  <h2 class="sec-title script" style="top:856px">Our Categories</h2>
  <p class="abs sec-sub">The process couldn't be any easier. Simply upload your photo, choose your art style and size, and let our team of skilled digital artists do the rest.</p>
  <div class="big-arrow" style="left:39px;top:1269px">‹</div>
  <div class="big-arrow" style="left:1128px;top:1269px">›</div>

  <div class="card card-side" style="left:110px">
    <div class="ph" role="img" aria-label="Watercolor painting of a mother and baby" style="background:linear-gradient(150deg,#f4d2c6,#f8ebe6)"></div>
    <h3>Watercolor</h3><div class="stars">★★★★★</div>
    <p>The artwork is delivered to your door FREE and ready to hang. Makes a perfect gift!</p>
    <div class="small-btn">Learn More</div>
  </div>
  <div class="card card-main">
    <div class="ph" role="img" aria-label="Oil painting of a bride holding a bouquet" style="background:linear-gradient(160deg,#3b3a2a,#8c6d4f 50%,#c9c9a0)"></div>
    <h3>Oil</h3><div class="stars">★★★★★</div>
    <p>Our talented team of artists can turn your digital photo into a one-of-a-kind canvas art piece, designed specifically for you!</p>
    <div class="btn" style="left:94px;top:460px;width:168px;height:48px;font-size:16px">Learn More</div>
  </div>
  <div class="card card-side" style="left:811px">
    <div class="ph" role="img" aria-label="Impressionist painting of a traveller by a canal" style="background:linear-gradient(160deg,#8fb7c9,#3f8f9a 55%,#b9453a)"></div>
    <h3>Impressionist</h3><div class="stars">★★★★★</div>
    <p>The artwork is delivered to your door FREE and ready to hang. Makes a perfect gift!</p>
    <div class="small-btn">Learn More</div>
  </div>
</section>

<section>
  <div class="abs about-bg"></div>
  <div class="abs about-photo" role="img" aria-label="Watercolor artwork of a mother kissing her baby"></div>
  <div class="abs about-card">
    <h2 class="script">About Easel House</h2>
    <p>At Easel House, we take your digital photo and turn it into a one-of-a-kind piece of artwork!The process couldn't be any easier. Simply upload your photo, choose your art style and size, and let our team of skilled digital artists do the rest.</p>
    <p style="margin-top:22px">Do you want to put your digital photo on canvas without an art style? No problem! Just choose the "Digital Photo/Retouching" category and upload your photo.</p>
  </div>
  <div class="btn" style="left:259px;top:2085px;width:167px;height:51px;font-size:16px">Read More</div>
</section>

<section>
  <h2 class="sec-title script" style="top:2286px">Why Us?</h2>
  <div class="why" style="left:107px;top:2380px">
    <svg width="80" height="84" viewBox="0 0 80 84"><path d="M40 6a24 24 0 0 0-14 44v10h28V50A24 24 0 0 0 40 6z" fill="none" stroke="#222" stroke-width="3"/><path d="M28 66h24M31 73h18" stroke="#e03a13" stroke-width="3"/><path d="M40 14v36M32 22v22M48 22v22" stroke="#e03a13" stroke-width="2.5"/></svg>
    <h4>Your Idea Your Design</h4>
    <p>Each art piece is customized for you! You choose your size, orientation and art style. Makes a perfect gift!!!</p>
  </div>
  <div class="why" style="left:440px;top:2380px">
    <svg width="120" height="84" viewBox="0 0 120 84"><circle cx="40" cy="34" r="24" fill="none" stroke="#e03a13" stroke-width="3"/><path d="M40 34l10-10" stroke="#222" stroke-width="3"/><path d="M30 62h70V44l-12-14H70v32" fill="none" stroke="#222" stroke-width="3"/><circle cx="42" cy="68" r="7" fill="#fff" stroke="#222" stroke-width="3"/><circle cx="88" cy="68" r="7" fill="#fff" stroke="#222" stroke-width="3"/></svg>
    <h4>Fast Shipping</h4>
    <p>Your artwork is printed and shipped in the USA! We offer fast turnaround with transit times typically 3-7 days. Free tracking with each order!!</p>
  </div>
  <div class="why" style="left:793px;top:2380px">
    <svg width="90" height="84" viewBox="0 0 90 84"><circle cx="45" cy="52" r="24" fill="none" stroke="#222" stroke-width="3"/><rect x="33" y="48" width="7" height="16" fill="#e03a13"/><path d="M42 64h14l3-14H48l2-10-8 10z" fill="#e03a13"/><path d="M45 4l3 7h7l-6 4 2 7-6-4-6 4 2-7-6-4h7z" fill="none" stroke="#e03a13" stroke-width="2"/><path d="M18 16l2 5h5l-4 3 1 5-4-3-4 3 1-5-4-3h5zM72 16l2 5h5l-4 3 1 5-4-3-4 3 1-5-4-3h5z" fill="none" stroke="#222" stroke-width="2"/></svg>
    <h4>High Quality</h4>
    <p>We've put a lot of effort ensuring your artwork is of the highest quality. Each piece is printed on the highest quality, gallery grade canvas.</p>
  </div>
</section>

<section>
  <div class="abs gallery-bg"></div>
  <h2 class="sec-title script" style="top:2722px">From photo to museum Quality canvas art</h2>
  <div class="ph" role="img" aria-label="Painting of a father and child walking on a beach" style="left:12px;top:2808px;width:281px;height:277px;background:linear-gradient(170deg,#d8c6a4,#8aa0b3 60%,#c7b48f)"></div>
  <div class="ph" role="img" aria-label="Painting of a wedding couple among flowers" style="left:303px;top:2808px;width:280px;height:277px;background:linear-gradient(160deg,#4c6b33,#a08360 55%,#e3dccf)"></div>
  <div class="ph" role="img" aria-label="Painting of a merle puppy" style="left:592px;top:2808px;width:293px;height:277px;background:linear-gradient(160deg,#c3c9c9,#7b7f7f 55%,#d6d2cc)"></div>
  <div class="ph" role="img" aria-label="Painting of a grandmother hugging a grandfather" style="left:895px;top:2808px;width:295px;height:277px;background:linear-gradient(160deg,#dfe3db,#7f8f6a 55%,#9cc2d3)"></div>
  <div class="ph" role="img" aria-label="Painting of a rider jumping a horse" style="left:12px;top:3096px;width:372px;height:277px;background:linear-gradient(160deg,#b8d4e8,#7a4a2a 55%,#dfeaf2)"></div>
  <div class="ph" role="img" aria-label="Painting of a dog and a cat resting together" style="left:396px;top:3096px;width:391px;height:277px;background:linear-gradient(160deg,#2f2a24,#8a5a2c 55%,#d68a3a)"></div>
  <div class="ph" role="img" aria-label="Watercolor of a mother kissing her baby" style="left:799px;top:3096px;width:391px;height:277px;background:linear-gradient(160deg,#fbf2ee,#f1cbbd 55%,#fbf4f1)"></div>
</section>

<section>
  <div class="abs deal"></div>
  <div class="abs badge"><div class="b1">DEAL</div><div class="b2">OF THE</div><div class="b3">WEEK</div><div class="b4">★★★★★</div></div>
  <div class="abs deal-text">
    <div class="pct">20% Off</div>
    <div class="sub">Digital Photo</div>
    <p>You will receive a proof in your email to approve within 1-2 days.</p>
    <p style="margin-top:26px">Once approved, your customized artwork will be transferred to canvas and shipped from our design studio in Florida.</p>
  </div>
  <div class="timer" style="left:350px"><b>03</b><span>Day</span></div>
  <div class="timer" style="left:427px"><b>12</b><span>Hours</span></div>
  <div class="timer" style="left:504px"><b>20</b><span>Min</span></div>
  <div class="timer" style="left:581px"><b>10</b><span>Sec</span></div>
  <div class="abs learn">Learn More</div>
  <div class="abs deal-photo" role="img" aria-label="Photo of two children sharing an ice cream cone"></div>
</section>

<footer class="site-footer">
  <div class="abs footer"></div>
  <div class="abs flinks"><span>Home</span><span class="sep">●</span><span>About Us</span><span class="sep">●</span><span>My orders</span><span class="sep">●</span><span>Testimonials</span><span class="sep">●</span><span>Our Category</span><span class="sep">●</span><span>Contact Us</span></div>
  <div class="abs fline" style="left:110px;top:4180px;width:980px;height:1px"></div>
  <div class="abs fbrand"><span class="dot"></span>Easel House</div>
  <div class="abs fline" style="left:436px;top:4180px;width:1px;height:231px"></div>
  <div class="abs fline" style="left:771px;top:4180px;width:1px;height:231px"></div>
  <div class="fcol" style="left:110px;width:326px"><h5>GET SOCIAL</h5><p style="font-size:15px">Follow us on social networks</p><div class="soc"><i></i><i></i><i></i><i></i></div></div>
  <div class="fcol" style="left:436px;width:335px"><h5>WE ARE HERE</h5><p>Easel House, United States<br>info@easelhouseart.com<br>+1 888 888 8888</p></div>
  <div class="fcol" style="left:771px;width:319px"><h5>LET'S TALK</h5><p style="line-height:24px">Here a questions or just want<br>to say hello?</p><p style="margin-top:10px;text-decoration:underline;font-size:14px">SEND US MESSAGE</p></div>
  <div class="abs fline" style="left:110px;top:4411px;width:980px;height:1px"></div>
  <div class="abs copy">Copyrights@2023.Easel House.All Rights Reserved</div>
  <div class="abs pay" style="left:874px"></div>
  <div class="abs pay" style="left:914px"></div>
  <div class="abs pay" style="left:954px"></div>
  <div class="abs pay" style="left:994px"></div>
  <div class="abs pay" style="left:1034px"></div>
  <div class="abs pay" style="left:1074px;width:16px"></div>
</footer>

</body>
</html>
```